Corvel Capital LLC

Need Professional Business cards for New Investment Fund

Target Market(s)

High Quality investors

Industry/Entity Type

Financial

Contact Information for Business Card

Phone Number +1 555 284 6190
Name Lukas Varenko
Title Fund Manager
email lv@FundCorvel.com
Website www.FundCorvel.com

Colors

Designer to choose colors to be used in the design.

Requirements
Must have
• Must have our Logo and all of the above. Must be made so lettering and loge can be raised

```html
<!DOCTYPE html>
<html lang="en">
<head>
<meta charset="utf-8">
<title>Orvanel – Business Card</title>
<link rel="stylesheet" href="https://fonts.googleapis.com/css2?family=Jost:wght@500;600&family=Montserrat:wght@400;500&display=swap">
<style>
  :root {
    --page-bg: #d9d7d4;
    --card-bg: #2f2f31;
    --card-back-bg: #262628;
    --pattern-tone: #343436;
    --accent-green: #2fd41a;
    --text-white: #f2f2f2;
    --divider: #bdbdbd;
  }
  * { box-sizing: border-box; margin: 0; padding: 0; }
  html, body {
    width: 1200px; height: 800px; overflow: hidden;
    background: var(--page-bg);
  }
  .sheet {
    width: 1200px; height: 800px;
    display: flex; flex-direction: column;
    align-items: center; justify-content: center; gap: 40px;
  }
  .card {
    position: relative;
    width: 560px; height: 320px;
    border-left: 3px solid var(--accent-green);
    border-bottom: 3px solid var(--accent-green);
    overflow: hidden;
  }
  .card--back { background: var(--card-back-bg); }
  .back-texture {
    position: absolute; inset: 0;
    background: linear-gradient(135deg, var(--pattern-tone), var(--card-back-bg));
  }
  .back-mark {
    position: absolute; right: 34px; bottom: 30px;
    display: flex; align-items: center; gap: 6px;
    font-family: "Jost", sans-serif; font-weight: 600;
    font-size: 15px; letter-spacing: 1px; color: var(--text-white);
  }
  .mark-square { width: 8px; height: 8px; background: var(--accent-green); }
  .card--front { background: var(--card-bg); }
  .brand {
    position: absolute; left: 330px; top: 92px;
    display: flex; align-items: center; gap: 10px;
    font-family: "Jost", sans-serif; font-weight: 600;
    font-size: 30px; letter-spacing: 3px; color: var(--text-white);
    white-space: nowrap;
  }
  .brand .mark-square { width: 14px; height: 14px; }
  .identity {
    position: absolute; right: 268px; top: 210px;
    text-align: right; white-space: nowrap;
  }
  .identity__name {
    font-family: "Jost", sans-serif; font-weight: 600;
    font-size: 21px; letter-spacing: 0.5px; color: var(--accent-green);
    text-transform: uppercase; line-height: 1.1;
  }
  .identity__title {
    font-family: "Montserrat", sans-serif; font-weight: 400;
    font-size: 15px; color: var(--text-white); margin-top: 2px;
  }
  .divider {
    position: absolute; left: 312px; top: 208px;
    width: 1px; height: 78px; background: var(--divider);
  }
  .contacts {
    position: absolute; left: 330px; top: 214px;
    list-style: none;
    font-family: "Montserrat", sans-serif; font-weight: 500;
    font-size: 14.5px; color: var(--text-white);
    white-space: nowrap;
  }
  .contacts li { display: flex; align-items: center; gap: 8px; height: 22px; }
  .contacts svg { width: 13px; height: 13px; fill: var(--accent-green); flex: none; }
</style>
</head>
<body>
<main class="sheet">
  <section class="card card--back" aria-label="Card back">
    <div class="back-texture" role="img" aria-label="Subtle tone-on-tone repeating brand texture"></div>
    <div class="back-mark"><span class="mark-square"></span>ORVANEL</div>
  </section>

  <section class="card card--front" aria-label="Card front">
    <div class="brand"><span class="mark-square"></span>ORVANEL</div>

    <div class="identity">
      <p class="identity__name">Lukas Varenko</p>
      <p class="identity__title">Fund Manager</p>
    </div>

    <div class="divider"></div>

    <ul class="contacts">
      <li>
        <svg viewBox="0 0 24 24" aria-hidden="true"><path d="M6.6 10.8a15.1 15.1 0 0 0 6.6 6.6l2.2-2.2a1 1 0 0 1 1-.25 11.4 11.4 0 0 0 3.6.57 1 1 0 0 1 1 1V20a1 1 0 0 1-1 1A17 17 0 0 1 3 4a1 1 0 0 1 1-1h3.5a1 1 0 0 1 1 1c0 1.25.2 2.45.57 3.57a1 1 0 0 1-.25 1z"/></svg>
        +1 555 284 6190
      </li>
      <li>
        <svg viewBox="0 0 24 24" aria-hidden="true"><path d="M2 5h20v14H2z M3.5 6.5 12 13l8.5-6.5" fill="none" stroke="var(--accent-green)" stroke-width="2.4"/></svg>
        lv@FundCorvel.com
      </li>
      <li>
        <svg viewBox="0 0 24 24" aria-hidden="true"><circle cx="12" cy="12" r="10" fill="none" stroke="var(--accent-green)" stroke-width="2.4"/><path d="M2 12h20M12 2c3 3 3 17 0 20M12 2c-3 3-3 17 0 20" fill="none" stroke="var(--accent-green)" stroke-width="2"/></svg>
        www.FundCorvel.com
      </li>
    </ul>
  </section>
</main>
</body>
</html>
```